Gobal construction supply company needs new business card design

I need a business card design for my global supply company using an existing logo. i will be looking to print these on rounded corner cards with the black background version of my logo on the back. on the front white background, my logo again and my simple details.

```html
<!DOCTYPE html>
<html lang="en">
<head>
<meta charset="UTF-8">
<title>Northgate Building Supply — Business Cards</title>
<link href="https://fonts.googleapis.com/css2?family=Oswald:wght@500&family=Work+Sans:wght@400;600&display=swap" rel="stylesheet">
<style>
  :root {
    --stage: #2a2a2a;
    --card-dark: #1e1e1e;
    --card-dark-edge: #2f2f2f;
    --card-light: #ffffff;
    --brand-red: #d71f26;
    --ink: #1d1d1d;
    --faint-red: #fbe3e4;
    --divider: #1d1d1d;
  }
  * { margin: 0; padding: 0; box-sizing: border-box; }
  html, body { width: 1200px; height: 900px; overflow: hidden; }
  body {
    background: var(--stage);
    font-family: "Work Sans", Arial, sans-serif;
    position: relative;
  }
  .card {
    position: absolute;
    left: 280px;
    width: 640px;
    height: 366px;
    border-radius: 18px;
    overflow: hidden;
  }
  .card--back {
    top: 60px;
    background: linear-gradient(135deg, var(--card-dark) 0%, var(--card-dark) 55%, var(--card-dark-edge) 100%);
    display: flex;
    align-items: center;
    justify-content: center;
  }
  .brand-lockup {
    display: flex;
    align-items: center;
    gap: 16px;
  }
  .brand-name {
    color: #ffffff;
    font-family: "Work Sans", Arial, sans-serif;
    font-weight: 600;
    font-size: 28px;
    letter-spacing: 1px;
    text-transform: uppercase;
  }
  .brand-dot {
    width: 26px;
    height: 26px;
    border-radius: 50%;
    background: var(--brand-red);
  }
  .card--front {
    top: 470px;
    background: var(--card-light);
  }
  .front-accent {
    position: absolute;
    left: 400px;
    top: 70px;
    width: 90px;
    height: 90px;
    border-radius: 50%;
    background: var(--faint-red);
  }
  .holder {
    position: absolute;
    right: 370px;
    top: 120px;
    text-align: right;
  }
  .holder__name {
    font-family: "Oswald", Arial, sans-serif;
    font-weight: 500;
    font-size: 40px;
    line-height: 1;
    color: var(--brand-red);
    text-transform: uppercase;
  }
  .holder__role {
    font-size: 19px;
    color: var(--ink);
    margin-top: 6px;
  }
  .divider {
    position: absolute;
    left: 288px;
    top: 128px;
    width: 3px;
    height: 62px;
    background: var(--divider);
  }
  .contact-list {
    position: absolute;
    left: 308px;
    top: 128px;
    list-style: none;
  }
  .contact-list li {
    display: flex;
    align-items: center;
    gap: 10px;
    font-size: 18px;
    line-height: 24px;
    color: var(--ink);
    letter-spacing: 0.5px;
  }
  .contact-list svg { width: 12px; height: 12px; flex: none; }
  .address {
    position: absolute;
    left: 80px;
    bottom: 48px;
    font-size: 19px;
    color: var(--ink);
    letter-spacing: 0.5px;
  }
</style>
</head>
<body>
  <section class="card card--back" aria-label="Card back">
    <div class="brand-lockup">
      <span class="brand-name">Northgate Building Supply</span>
      <span class="brand-dot"></span>
    </div>
  </section>

  <section class="card card--front" aria-label="Card front">
    <div class="front-accent"></div>
    <div class="holder">
      <div class="holder__name">Daniel Carter</div>
      <div class="holder__role">Director</div>
    </div>
    <div class="divider"></div>
    <ul class="contact-list">
      <li>
        <svg viewBox="0 0 12 12" aria-hidden="true"><path d="M2.5 1 L4.5 1 L5 3.5 L3.8 4.3 Q4.8 6.8 7.7 8.2 L8.5 7 L11 7.5 L11 9.5 Q11 11 9.5 11 Q1 10 1 2.5 Q1 1 2.5 1Z" fill="var(--brand-red)"/></svg>
        555-014-2298
      </li>
      <li>
        <svg viewBox="0 0 12 12" aria-hidden="true"><rect x="1" y="2.5" width="10" height="7" fill="none" stroke="var(--brand-red)" stroke-width="1.3"/><path d="M1 2.5 L6 6.5 L11 2.5" fill="none" stroke="var(--brand-red)" stroke-width="1.3"/></svg>
        info@northgatesupply.com
      </li>
      <li>
        <svg viewBox="0 0 12 12" aria-hidden="true"><circle cx="6" cy="6" r="5" fill="none" stroke="var(--brand-red)" stroke-width="1.2"/><ellipse cx="6" cy="6" rx="2.2" ry="5" fill="none" stroke="var(--brand-red)" stroke-width="1"/><line x1="1" y1="6" x2="11" y2="6" stroke="var(--brand-red)" stroke-width="1"/></svg>
        www.northgatesupply.com
      </li>
    </ul>
    <p class="address">48 Harbour Road Box 902, Cedar Bay, AB</p>
  </section>
</body>
</html>
```